4th Generation Family Business Needs a New Card Design!

We are a family owned 4th Generation company. We are based in the Sydney, Australia area and we are desperately in need of a more modern and classy card. We are monumental masons who design, supply & erect lasting memorials throughout cemeteries in Sydney. Our customers are normally in a period of grieving. I have attached logo files that will need to be implemented on the card. Company was established 1935. Australian Owned and Operated. Card needs to be designed to PIXO.com specification.

Target Market(s)

Our target market is based upon people that a grieving for family members that have passed away. We also deal with alot of companies that own and operate cemeteries.

Industry/Entity Type

Business

Contact Information for Business Card

Simon Harcourt, Operations Manager, 0417293086, simon@harcourtmemorials.com.au
Lewis Harcourt, Director, 0491630572, lewis@harcourtmemorials.com.au
Phone # 02 9561 3048
Website: www.harcourtmemorials.com.au
Address: Suite 17, 8 Palfrey Lane, West Carlow, Sydney NSW 2156

Font styles to use
Serif
Decorative
Script

Requirements
Must have
• Would like to see the logo nicely implemented with a modern design. Embossed lettering would be a nice additive.

```html
<!DOCTYPE html>
<html lang="en">
<head>
<meta charset="utf-8">
<title>Harcourt Memorials – Business Card</title>
<link rel="stylesheet" href="https://fonts.googleapis.com/css2?family=Cinzel:wght@400&family=Arimo:wght@400&display=swap">
<style>
  :root {
    --backdrop: #d8d8d8;
    --card-stock: #f5f5f3;
    --ink: #1e1e1e;
    --gold: #e8b92b;
    --emboss: #dcdcdc;
  }
  * { margin: 0; padding: 0; box-sizing: border-box; }
  html, body {
    width: 980px;
    height: 1200px;
    overflow: hidden;
    background: var(--backdrop);
  }
  .canvas {
    position: relative;
    width: 980px;
    height: 1200px;
  }
  .card {
    position: absolute;
    left: 137px;
    width: 706px;
    height: 474px;
    background: var(--card-stock);
    text-align: center;
  }
  .card--front { top: 108px; }
  .card--back { top: 631px; }

  .brand-mark {
    position: absolute;
    left: 50%;
    width: 130px;
    height: 130px;
    margin-left: -65px;
  }
  .card--front .brand-mark { top: 122px; background: var(--emboss); }
  .card--back .brand-mark { top: 55px; background: var(--ink); }

  .brand-name {
    position: absolute;
    left: 0; right: 0;
    font-family: "Cinzel", serif;
    font-weight: 400;
    font-size: 34px;
    letter-spacing: 2px;
    line-height: 1;
  }
  .card--front .brand-name { top: 280px; color: var(--emboss); }
  .card--back .brand-name { top: 212px; color: var(--ink); }

  .address {
    position: absolute;
    left: 0; right: 0;
    top: 374px;
    font-family: "Arimo", sans-serif;
    font-style: normal;
    font-size: 18px;
    line-height: 32px;
    color: var(--ink);
  }

  .person__name {
    position: absolute;
    left: 0; right: 0;
    top: 292px;
    font-family: "Cinzel", serif;
    font-weight: 400;
    font-size: 34px;
    line-height: 1;
    letter-spacing: 1px;
    color: var(--ink);
  }
  .person__role {
    position: absolute;
    left: 0; right: 0;
    top: 334px;
    font-family: "Cinzel", serif;
    font-size: 18px;
    line-height: 1;
    letter-spacing: 2px;
    color: var(--gold);
  }
  .contact {
    position: absolute;
    left: 0; right: 0;
    top: 372px;
    font-family: "Arimo", sans-serif;
    font-size: 17px;
    line-height: 30px;
    color: var(--ink);
  }
  .contact__sep { padding: 0 4px; }
</style>
</head>
<body>
<main class="canvas">
  <section class="card card--front" aria-label="Card front">
    <div class="brand-mark" aria-hidden="true"></div>
    <p class="brand-name">HARCOURT MEMORIALS</p>
    <address class="address">
      Suite 17, 8 Palfrey Lane<br>
      West Carlow, Sydney NSW 2156
    </address>
  </section>

  <section class="card card--back" aria-label="Card back">
    <div class="brand-mark" aria-hidden="true"></div>
    <p class="brand-name">HARCOURT MEMORIALS</p>
    <h1 class="person__name">SIMON HARCOURT</h1>
    <p class="person__role">OPERATIONS MANAGER</p>
    <p class="contact">
      02 9561 3048<span class="contact__sep">|</span>0417293086<span class="contact__sep">|</span>simon@harcourtmemorials.com.au<br>
      www.harcourtmemorials.com.au
    </p>
  </section>
</main>
</body>
</html>
```